Moravel Aesthetic Doctor

I require an elegant, luxurious looking business card for my aesthetic business. I am a doctor and that will set me aside from competitors. I am planning to provide home and spa based treatments to clients with high expectations. I have attached my logo.

```html
<!DOCTYPE html>
<html lang="en">
<head>
<meta charset="utf-8">
<title>Moravel Aesthetic Doctor – Business Card</title>
<link rel="stylesheet" href="https://fonts.googleapis.com/css2?family=Open+Sans:wght@400;600&display=swap">
<style>
  :root {
    --bg: #e6e6e6;
    --card: #f4f4f4;
    --ink: #2b2b2b;
    --grey: #9a9a9a;
    --accent: #1aa3e0;
    --band-1: #a3d6ea;
    --band-2: #7cc4e4;
    --band-3: #53aad9;
    --band-4: #2f90cc;
    --band-5: #1c79bd;
    --band-6: #1c6bb0;
  }
  * { margin: 0; padding: 0; box-sizing: border-box; }
  html, body { width: 1200px; height: 960px; overflow: hidden; }
  body {
    background: var(--bg);
    font-family: "Open Sans", Arial, sans-serif;
    color: var(--ink);
    position: relative;
  }
  .card {
    position: absolute;
    left: 320px;
    width: 560px;
    height: 342px;
    background: var(--card);
    overflow: hidden;
  }
  .card--front { top: 120px; }
  .card--back { top: 498px; }

  .colour-band {
    position: absolute;
    left: 0; right: 0; bottom: 0;
    height: 16px;
    display: flex;
  }
  .colour-band span { flex: 1; }
  .colour-band span:nth-child(1) { background: var(--band-1); }
  .colour-band span:nth-child(2) { background: var(--band-2); }
  .colour-band span:nth-child(3) { background: var(--band-3); }
  .colour-band span:nth-child(4) { background: var(--band-4); }
  .colour-band span:nth-child(5) { background: var(--band-5); }
  .colour-band span:nth-child(6) { background: var(--band-6); }

  /* Front */
  .brand-lockup {
    position: absolute;
    left: 0; right: 0;
    top: 130px;
    display: flex;
    align-items: center;
    justify-content: center;
    gap: 18px;
  }
  .brand-mark {
    width: 56px; height: 56px;
    border: 3px solid var(--grey);
    border-radius: 50%;
  }
  .brand-name {
    font-size: 34px;
    font-weight: 400;
    color: var(--grey);
    letter-spacing: 1px;
  }
  .tagline {
    position: absolute;
    left: 0; right: 0;
    top: 284px;
    text-align: center;
    font-size: 18px;
  }

  /* Back */
  .back-brand {
    position: absolute;
    right: 32px;
    top: 40px;
    display: flex;
    align-items: center;
    gap: 12px;
  }
  .back-brand .brand-mark { width: 40px; height: 40px; border-width: 2px; }
  .back-brand .brand-name { font-size: 22px; }

  .doctor {
    position: absolute;
    left: 38px;
    top: 126px;
  }
  .doctor-name { font-size: 19px; line-height: 24px; }
  .doctor-name small { font-size: 12px; color: var(--accent); margin-left: 2px; }
  .doctor-diploma { font-size: 14px; color: var(--accent); line-height: 20px; }

  .divider {
    position: absolute;
    left: 38px;
    top: 186px;
    width: 334px;
    height: 1px;
    background: var(--accent);
  }

  .contacts {
    position: absolute;
    left: 38px;
    top: 198px;
    list-style: none;
    font-size: 16px;
    line-height: 21px;
  }
  .contacts li { display: flex; align-items: center; gap: 5px; }
  .contacts svg { width: 13px; height: 13px; fill: none; stroke: var(--accent); stroke-width: 1.6; }
  .contacts .icon-phone { fill: var(--accent); stroke: none; }

  .social {
    position: absolute;
    left: 39px;
    top: 287px;
    display: flex;
    gap: 5px;
  }
  .social span {
    width: 12px; height: 12px;
    border-radius: 50%;
    background: var(--accent);
  }

  .services {
    position: absolute;
    right: 31px;
    top: 178px;
    list-style: none;
    text-align: right;
    font-size: 17px;
    line-height: 21px;
  }
</style>
</head>
<body>

<section class="card card--front" aria-label="Business card front">
  <div class="brand-lockup">
    <span class="brand-mark" aria-hidden="true"></span>
    <span class="brand-name">Moravel Aesthetic Doctor</span>
  </div>
  <p class="tagline">Home and Spa Based Treatments</p>
  <div class="colour-band"><span></span><span></span><span></span><span></span><span></span><span></span></div>
</section>

<section class="card card--back" aria-label="Business card back">
  <div class="back-brand">
    <span class="brand-mark" aria-hidden="true"></span>
    <span class="brand-name">Moravel</span>
  </div>

  <div class="doctor">
    <p class="doctor-name">Dr Lena Voss <small>MRCPCH MD</small></p>
    <p class="doctor-diploma">Australasian Diploma of Aesthetic Medicine</p>
  </div>

  <div class="divider"></div>

  <ul class="contacts">
    <li>
      <svg class="icon-phone" viewBox="0 0 16 16" aria-hidden="true"><path d="M3.2 1.2l2.4 0 1.2 3.4-1.6 1.2c.8 1.8 2.2 3.2 4 4l1.2-1.6 3.4 1.2v2.4c0 1-1 2-2 2C6.2 13.8 2.2 9.8 1.2 3.2c0-1 1-2 2-2z"/></svg>
      0800 555 014
    </li>
    <li>
      <svg viewBox="0 0 16 16" aria-hidden="true"><rect x="1.5" y="3.5" width="13" height="9"/><path d="M1.5 3.5l6.5 5 6.5-5"/></svg>
      lena@moravel.co.nz
    </li>
    <li>
      <svg viewBox="0 0 16 16" aria-hidden="true"><circle cx="8" cy="8" r="6.5"/><ellipse cx="8" cy="8" rx="3" ry="6.5"/><path d="M1.5 8h13"/></svg>
      www.moravel.co.nz
    </li>
  </ul>

  <div class="social" aria-label="Social media">
    <span></span><span></span>
  </div>

  <ul class="services">
    <li>Dermal injectables</li>
    <li>Plasma facials</li>
    <li>Microneedling</li>
    <li>Skin boosters</li>
    <li>Excessive sweating</li>
    <li>Home and Spa Based Treatments</li>
  </ul>

  <div class="colour-band"><span></span><span></span><span></span><span></span><span></span><span></span></div>
</section>

</body>
</html>
```